Logo, Web and Mobile Designs for enterprise social media platform

All the details are in the attached document, please start reading the scope document first which explains what is this project about and the details about the needed deliverables, after that please read the UI_Requirements document which will detail what is expected regarding the coded web version since this is a coded contest, it is very important that you meet the UI requirements or suggest something else but we will need to agree first before working on the coded version

Good Luck

Target Market(s)

Enterprise Social Media

Industry/Entity Type

Media

Coding

Coded - Design and coding required

Number of Pages Required

5+ page

Font styles to use
Sans Serif

Requirements
Must have
• All the must haves are listed in the scope document so please check before you start

```html
<!DOCTYPE html>
<html lang="en">
<head>
<meta charset="UTF-8">
<title>Teamora – Social Media Platform</title>
<link href="https://fonts.googleapis.com/css2?family=Raleway:wght@400;500;700;800&family=Playfair+Display:wght@700&display=swap" rel="stylesheet">
<style>
  :root {
    --sky-top: #4f4b97;
    --sky-mid: #6f4f90;
    --sky-low: #8c5a83;
    --city-dark: #2f2438;
    --accent: #d7264f;
    --accent-bar: rgba(215, 38, 79, 0.92);
    --white: #ffffff;
    --nav-active: rgba(40, 38, 78, 0.55);
    --line: rgba(255, 255, 255, 0.9);
  }
  * { margin: 0; padding: 0; box-sizing: border-box; }
  html, body { width: 1200px; height: 631px; overflow: hidden; }
  body { font-family: "Raleway", sans-serif; color: var(--white); }

  .hero {
    position: relative;
    width: 1200px;
    height: 631px;
    overflow: hidden;
  }
  .hero-backdrop {
    position: absolute;
    inset: 0;
    background:
      linear-gradient(180deg, var(--sky-top) 0%, var(--sky-mid) 35%, var(--sky-low) 58%, #5a3c5e 72%, var(--city-dark) 100%);
  }

  .site-header {
    position: absolute;
    top: 0; left: 0; right: 0;
    height: 100px;
  }
  .brand {
    position: absolute;
    left: 88px;
    top: 25px;
    display: flex;
    align-items: center;
    gap: 12px;
  }
  .brand-mark {
    width: 46px; height: 46px;
    border-radius: 50%;
    background: var(--accent);
  }
  .brand-name {
    font-weight: 700;
    font-size: 24px;
    color: var(--white);
  }

  .main-nav {
    position: absolute;
    top: 36px;
    left: 490px;
    right: 87px;
    display: flex;
    justify-content: space-between;
    align-items: center;
  }
  .main-nav a {
    color: var(--white);
    text-decoration: none;
    font-size: 14px;
    font-weight: 500;
    line-height: 33px;
    padding: 0 13px;
    border-radius: 4px;
  }
  .main-nav a.is-active { background: var(--nav-active); }

  .hero-content {
    position: absolute;
    top: 190px;
    left: 87px;
    width: 1027px;
    text-align: center;
  }
  .eyebrow {
    display: flex;
    align-items: center;
    gap: 26px;
  }
  .eyebrow-rule {
    flex: 1;
    height: 5px;
    border-top: 1px solid var(--line);
    border-bottom: 1px solid var(--line);
  }
  .eyebrow-text {
    font-family: "Playfair Display", serif;
    font-weight: 700;
    font-size: 30px;
    letter-spacing: 0.5px;
    white-space: nowrap;
  }
  .hero-title {
    margin-top: 22px;
    font-weight: 800;
    font-size: 50px;
    letter-spacing: 0.5px;
    text-shadow: 2px 3px 3px rgba(0, 0, 0, 0.45);
  }

  .hero-actions {
    position: absolute;
    top: 334px;
    left: 405px;
    display: flex;
    gap: 33px;
  }
  .btn {
    height: 51px;
    width: 173px;
    display: flex;
    align-items: center;
    justify-content: center;
    gap: 18px;
    font-size: 21px;
    font-weight: 500;
    color: var(--white);
    text-decoration: none;
  }
  .btn-primary { background: var(--accent); }
  .btn-outline { border: 1px solid rgba(255, 255, 255, 0.85); }

  .social-bar {
    position: absolute;
    left: 219px;
    top: 579px;
    width: 761px;
    height: 52px;
    background: var(--accent-bar);
    border-radius: 20px 20px 0 0;
  }
  .social-link {
    position: absolute;
    top: 11px;
    display: flex;
    align-items: center;
    gap: 12px;
    color: var(--white);
    text-decoration: none;
    font-size: 16px;
  }
  .social-dot {
    width: 30px; height: 30px;
    border: 1.5px solid var(--white);
    border-radius: 50%;
  }
  .social-dot.is-filled { background: var(--white); }
</style>
</head>
<body>
  <section class="hero">
    <div class="hero-backdrop" role="img" aria-label="Evening city skyline with lit skyscrapers under a purple sky"></div>

    <header class="site-header">
      <div class="brand">
        <span class="brand-mark"></span>
        <span class="brand-name">Teamora</span>
      </div>
      <nav class="main-nav">
        <a href="#" class="is-active">HOME</a>
        <a href="#">ABOUT</a>
        <a href="#">EVENTS</a>
        <a href="#">MEDIA</a>
        <a href="#">PRICE</a>
        <a href="#">BLOG</a>
        <a href="#">CONTACT</a>
      </nav>
    </header>

    <div class="hero-content">
      <div class="eyebrow">
        <span class="eyebrow-rule"></span>
        <span class="eyebrow-text">GET CONNECTED WITH US</span>
        <span class="eyebrow-rule"></span>
      </div>
      <h1 class="hero-title">SOCIAL MEDIA PLATFORM</h1>
    </div>

    <div class="hero-actions">
      <a href="#" class="btn btn-primary">REGISTER
        <svg width="19" height="19" viewBox="0 0 20 20" aria-hidden="true">
          <circle cx="10" cy="10" r="10" fill="#ffffff"/>
          <path d="M5 10h8M9.5 6l4 4-4 4" stroke="#d7264f" stroke-width="2.4" fill="none" stroke-linecap="round" stroke-linejoin="round"/>
        </svg>
      </a>
      <a href="#" class="btn btn-outline">WATCH VIDEO</a>
    </div>

    <div class="social-bar">
      <a href="#" class="social-link" style="left:63px"><span class="social-dot"></span>Circlebook</a>
      <a href="#" class="social-link" style="left:333px"><span class="social-dot is-filled"></span>Chirpline</a>
      <a href="#" class="social-link" style="left:585px"><span class="social-dot"></span>Snapframe</a>
    </div>
  </section>
</body>
</html>
```